Corvane Business Cards

Front of business card will have logo, name, address, & telephone number. Back of card will have a list of services provided - Roads, Substation Pads, Temporary Pads, Site Pads, Land Leveling, Powerline Row Cleaning, Land Clearing, Gates, Fencing, Construction Entrances, Excavation, Trenching, Underground Utilities, Directional Boring, Pile Driving. We are a construction company that uses heavy equipment like bulldozers, motor graders/blades, dump trucks, backhoes, hydro axes, & skid loaders. We build roads, pads, & install electric utility lines & waterlines underground. This logo is new. The word "Construction" can be smaller as uploaded 2 example edited logos. We will be using this card design for many employees.
Target Market(s)
Industrial Electric Powerline, Wind Turbine, Solar Panel, & Water Utility companies.
Contact Information for Business Card
Name/Position - Dwayne Halster - Owner
Address: 4875 FM 309
Dunmore, OK 73521
Phone number - (580) 482-5096

```html
<!DOCTYPE html>
<html lang="en">
<head>
<meta charset="utf-8">
<title>Corvane Construction – Business Cards</title>
<link href="https://fonts.googleapis.com/css2?family=Marcellus&family=Arimo:wght@400;700&display=swap" rel="stylesheet">
<style>
  :root {
    --backdrop: #141414;
    --card-stock: #ecebe6;
    --ink-maroon: #4a1b21;
    --ink-grey: #6f6a66;
    --rule-grey: #a9a5a0;
  }
  * { box-sizing: border-box; margin: 0; padding: 0; }
  html, body {
    width: 1200px; height: 822px; overflow: hidden;
    background: var(--backdrop);
  }
  .sheet {
    width: 1200px; height: 822px;
    display: flex; align-items: center; justify-content: center; gap: 48px;
  }
  .card {
    width: 525px; height: 300px;
    background: var(--card-stock);
    color: var(--ink-maroon);
    position: relative;
  }
  /* Front */
  .card-front {
    display: flex; flex-direction: column; align-items: center;
    padding-top: 58px;
    font-family: "Marcellus", serif;
  }
  .brand-name {
    font-size: 52px; letter-spacing: 4px; line-height: 1;
  }
  .brand-tagline {
    font-size: 25px; letter-spacing: 2px; margin-top: 6px;
  }
  .person-name {
    font-size: 21px; letter-spacing: 3px; margin-top: 16px;
  }
  .person-role {
    font-family: "Arimo", sans-serif; font-size: 12px;
    color: var(--ink-grey); margin-top: 4px;
  }
  .person-rule {
    width: 90px; height: 1px; background: var(--rule-grey); margin-top: 5px;
  }
  .contact-line {
    position: absolute; left: 0; right: 0; bottom: 26px;
    text-align: center; white-space: nowrap;
    font-family: "Arimo", sans-serif; font-size: 13px; color: var(--ink-grey);
  }
  .contact-line .label { color: var(--ink-maroon); font-weight: 700; }
  /* Back */
  .card-back {
    display: flex; flex-direction: column; align-items: center; justify-content: center;
    padding: 0 34px;
    font-family: "Arimo", sans-serif; font-size: 12.5px; line-height: 1.45;
    text-align: center;
  }
  .back-rule {
    width: 210px; height: 1px; background: var(--rule-grey); margin: 10px 0;
  }
</style>
</head>
<body>
<main class="sheet">
  <section class="card card-front">
    <div class="brand-name">CORVANE</div>
    <div class="brand-tagline">CONSTRUCTION</div>
    <div class="person-name">DWAYNE HALSTER</div>
    <div class="person-role">Owner</div>
    <div class="person-rule"></div>
    <p class="contact-line"><span class="label">P:</span> (580) 482-5096 &nbsp;|&nbsp; 4875 FM 309 Dunmore, OK 73521</p>
  </section>

  <section class="card card-back">
    <p class="services-list">Roads, Substation Pads | Temporary Pads | Site Pads,<br>
      Land Leveling | Powerline Row Cleaning | Land Clearing<br>
      Gates | Fencing Construction Entrances | Excavation<br>
      Trenching | Underground Utilities | Directional Boring | Pile Driving.</p>
    <div class="back-rule"></div>
    <p class="equipment-note">We are a construction company that uses heavy equipment<br>
      like bulldozers | motor graders/blades | dump trucks<br>
      backhoes | hydro axes &amp; skid loaders.</p>
    <div class="back-rule"></div>
    <p class="work-note">We build roads, pads<br>
      install electric utility lines &amp; waterlines underground.</p>
  </section>
</main>
</body>
</html>
```